stationary deign for trucking company

im a trucking company looking for a professional set of stationary designs i deliver goods from point a to b
Updates

When submitting stationary designs I need envelope design, letterhead, cards, I’d badge etc

Industry/Entity Type

Trucking Company

Requirements
Must have
• must have letter head, business card, envelope, fax sheet, id badge, folder, thank you card, notebook, invoice sheet.
Nice to have
• nice to have them all custom made (letterhead,envelope, business card, I’d badge etc
Should not have
• must not have prepaid sign want i unique design for items

```html
<!DOCTYPE html>
<html lang="en">
<head>
<meta charset="utf-8">
<title>Harlow Freight + Logistics – Business Card</title>
<link rel="stylesheet" href="https://fonts.googleapis.com/css2?family=Montserrat:wght@500;600&family=Open+Sans:wght@400;600;700&display=swap">
<style>
  :root {
    --backdrop: #3b3c3f;
    --card: #ffffff;
    --card-shade: #f1f1f1;
    --brand-blue: #0a53a3;
    --ink: #111111;
    --body-text: #3a3a3a;
    --on-blue: #ffffff;
  }
  * { box-sizing: border-box; margin: 0; padding: 0; }
  html, body { width: 1200px; height: 1000px; overflow: hidden; }
  body {
    background: var(--backdrop);
    font-family: "Open Sans", Arial, sans-serif;
    position: relative;
  }
  .card {
    position: absolute;
    left: 250px;
    width: 700px;
    height: 400px;
    background: linear-gradient(160deg, var(--card) 55%, var(--card-shade));
    box-shadow: 0 14px 30px rgba(0,0,0,0.45);
    overflow: hidden;
  }
  .card--back { top: 60px; }
  .card--front { top: 540px; }

  /* Wordmark */
  .wordmark { display: flex; flex-direction: column; font-family: "Montserrat", Arial, sans-serif; color: var(--ink); }
  .wordmark__name { font-weight: 600; letter-spacing: 0.18em; line-height: 1; }
  .wordmark__tag { font-weight: 600; letter-spacing: 0.26em; line-height: 1; margin-top: 6px; }

  .back-lockup {
    position: absolute; left: 0; right: 0; top: 150px;
    display: flex; align-items: center; justify-content: center; gap: 18px;
  }
  .back-lockup__square { width: 34px; height: 34px; background: var(--brand-blue); }
  .back-lockup .wordmark__name { font-size: 46px; }
  .back-lockup .wordmark__tag { font-size: 11.5px; }
  .back-web {
    position: absolute; left: 0; right: 0; top: 272px;
    text-align: center; font-size: 15px; letter-spacing: 0.32em; color: var(--body-text);
  }

  /* Front */
  .front-band { position: absolute; inset: 0; }
  .front-mark {
    position: absolute; left: 40px; top: 80px;
    display: flex; flex-direction: column; align-items: flex-start; gap: 18px;
  }
  .front-mark__square { width: 130px; height: 130px; background: var(--on-blue); }
  .front-mark__name {
    font-family: "Montserrat", Arial, sans-serif; font-weight: 600;
    font-size: 28px; letter-spacing: 0.16em; line-height: 1; color: var(--on-blue);
  }
  .front-wordmark { position: absolute; right: 38px; top: 34px; align-items: flex-end; }
  .front-wordmark .wordmark__name { font-size: 36px; }
  .front-wordmark .wordmark__tag { font-size: 9.5px; }
  .front-accent { position: absolute; right: 0; top: 150px; width: 16px; height: 36px; background: var(--brand-blue); }
  .contact { position: absolute; right: 40px; top: 140px; text-align: right; color: var(--body-text); }
  .contact__name { font-size: 22px; font-weight: 700; color: var(--brand-blue); letter-spacing: 0.04em; line-height: 1.1; }
  .contact__title { font-size: 16px; color: var(--ink); letter-spacing: 0.04em; margin-bottom: 10px; }
  .contact__address { font-size: 16px; line-height: 1.3; margin-bottom: 8px; }
  .contact__lines { list-style: none; font-size: 16px; line-height: 1.35; }
  .contact__lines li { display: flex; align-items: center; justify-content: flex-end; gap: 8px; }
  .contact__lines svg { width: 15px; height: 15px; fill: var(--brand-blue); flex: none; }
</style>
</head>
<body>

<section class="card card--back" aria-label="Business card back">
  <div class="back-lockup">
    <span class="back-lockup__square"></span>
    <div class="wordmark">
      <span class="wordmark__name">HARLOW</span>
      <span class="wordmark__tag">FREIGHT + LOGISTICS</span>
    </div>
  </div>
  <p class="back-web">harlowfreight.com</p>
</section>

<section class="card card--front" aria-label="Business card front">
  <svg class="front-band" viewBox="0 0 700 400" preserveAspectRatio="none" aria-hidden="true">
    <polygon points="0,0 300,0 170,400 0,400" fill="var(--brand-blue)"/>
  </svg>

  <div class="front-mark">
    <span class="front-mark__square"></span>
    <span class="front-mark__name">HARLOW</span>
  </div>

  <div class="wordmark front-wordmark">
    <span class="wordmark__name">HARLOW</span>
    <span class="wordmark__tag">FREIGHT + LOGISTICS</span>
  </div>

  <span class="front-accent"></span>

  <div class="contact">
    <p class="contact__name">MARK ELLERY</p>
    <p class="contact__title">PRESIDENT</p>
    <p class="contact__address">2170 Ridgeline Avenue<br>Glen Haven, NY 11020</p>
    <ul class="contact__lines">
      <li>555 0142 2210
        <svg viewBox="0 0 16 16"><path d="M3 1.5l3 0 1 3.5-1.8 1.2a8 8 0 0 0 4.6 4.6L11 9l3.5 1v3c0 .8-.7 1.5-1.5 1.5A12 12 0 0 1 1.5 3c0-.8.7-1.5 1.5-1.5z"/></svg>
      </li>
      <li>555 0178 5316
        <svg viewBox="0 0 16 16"><path d="M4.5 0h7c.8 0 1.5.7 1.5 1.5v13c0 .8-.7 1.5-1.5 1.5h-7C3.7 16 3 15.3 3 14.5v-13C3 .7 3.7 0 4.5 0zM4.5 2v10.5h7V2zM8 13.3a.9.9 0 1 0 0 1.8.9.9 0 0 0 0-1.8z"/></svg>
      </li>
      <li>555 0193 3846
        <svg viewBox="0 0 16 16"><path d="M4 1h6l2 2v3H4zM2 6.5h12c.6 0 1 .4 1 1V13c0 .6-.4 1-1 1H2c-.6 0-1-.4-1-1V7.5c0-.6.4-1 1-1zM4 11h8v1.5H4z"/></svg>
      </li>
      <li>mark@harlowfreight.com
        <svg viewBox="0 0 16 16"><path d="M1 3h14v1.2L8 9 1 4.2zM1 5.8l7 4.8 7-4.8V13H1z"/></svg>
      </li>
      <li>www.harlowfreight.com
        <svg viewBox="0 0 16 16"><path d="M8 .5a7.5 7.5 0 1 0 0 15 7.5 7.5 0 0 0 0-15zm0 1.6c.9 1.1 1.5 2.8 1.6 4.9H6.4C6.5 4.9 7.1 3.2 8 2.1zM2.1 7h2.7c.1-1.7.5-3.2 1.1-4.3A5.9 5.9 0 0 0 2.1 7zm0 2a5.9 5.9 0 0 0 3.8 4.3C5.3 12.2 4.9 10.7 4.8 9zm4.3 0h3.2c-.1 2.1-.7 3.8-1.6 4.9-.9-1.1-1.5-2.8-1.6-4.9zm4.8 0h2.7a5.9 5.9 0 0 1-3.8 4.3c.6-1.1 1-2.6 1.1-4.3zm2.7-2h-2.7c-.1-1.7-.5-3.2-1.1-4.3A5.9 5.9 0 0 1 13.9 7z"/></svg>
      </li>
    </ul>
  </div>
</section>

</body>
</html>
```